NEW Wordpress Website Design for a Dynamic Long Term Healthcare Company in Hawaii

I would like a new website design for my current company, Marlow Health Collective, which has two different brands - Marlow Homecare and Marlow Senior Living. You can see the current website at www.marlowhealth-example.com. The website should be built using Wordpress Software and the Framewise theme. The website should have a local Hawaii island/tropical feel, but look professional for healthcare. I'm looking for something fresh, and want the designer to select colors, styles, etc.

In the Header, on all pages, I would like a menu that includes Home Care, Senior Living, Rates, and About Us.
Under each of the Header Menu Titles, I would like these drop downs included:
Home Care (drop down pages)- Nurse Aide Care, 24-Hour Home Care, Skilled Nursing, Lifestyle Aide, Hospice at Home, Bathing & Meal Service.
Senior Living (drop down pages) - Long-Term Stay, Short-Term Stay.
Rates (drop down page) - Rates.
About Us (drop down pages) - Our Mission, Ohana Talk, About Dana Marlow.

In the footer, on all pages, you should include the address: 248 Pueo Lane, Suite 310, Honolulu, HI 96817. Phone number: 808-555-0172
The footer should also include buttons for a page called Learn, Caregiver Jobs, and each of the service page links to include: Nurse Aide Care, 24-Hour Home Care, Skilled Nursing, Lifestyle Aide, Hospice at Home, Bathing & Meal Service.
Please don't take the current website and redesign a few aspects. I'm looking for a completely different look and feel.

Target Market(s)

40-80 year olds

Industry/Entity Type

Long Term Healthcare

Coding

Coded - Design and coding required

Requirements
Should not have
• Our existing website as a template. We are looking for a complete redesign. Thank you.

```html
<!DOCTYPE html>
<html lang="en">
<head>
<meta charset="utf-8">
<title>Marlow Health Collective</title>
<link href="https://fonts.googleapis.com/css2?family=Montserrat:wght@400;500;600;700;800&display=swap" rel="stylesheet">
<style>
:root{
  --teal:#0f6b62;
  --teal-dark:#0b5a52;
  --teal-field:#4d8c85;
  --mint:#e3f1ec;
  --yellow:#f5cf4f;
  --coral:#f08a76;
  --ink:#1f2d2b;
  --muted:#55615f;
  --white:#ffffff;
}
*{box-sizing:border-box;margin:0;padding:0}
html,body{width:1200px;height:3560px;overflow:hidden}
body{font-family:"Montserrat",sans-serif;color:var(--ink);background:var(--white);position:relative}
.abs{position:absolute}
.btn{display:inline-block;background:var(--yellow);color:var(--ink);font-weight:600;border-radius:22px;font-size:14px;text-align:center}
.ph{border-radius:16px;border:3px solid var(--yellow)}
/* top bar */
.topbar{left:0;top:0;width:1200px;height:41px;background:var(--teal);color:#fff;font-size:13px}
.topbar .hours{left:116px;top:13px}
.topbar .hours svg{vertical-align:-3px;margin-right:6px}
.topbar .phone{left:832px;top:9px;font-size:18px;font-weight:600}
.topbar .btn{left:988px;top:7px;width:100px;height:28px;line-height:28px;font-size:12px}
/* header */
.header{left:0;top:41px;width:1200px;height:83px;background:#fff;border-bottom:1px solid #e4e4e4}
.brand{font-weight:600;color:var(--teal)}
.brand .mark{display:inline-block;width:16px;height:16px;background:var(--coral);border-radius:50%;margin-right:6px;vertical-align:middle}
.header .brand-l{left:112px;top:28px;font-size:22px}
.header .brand-r{left:1000px;top:30px;font-size:18px}
.nav{left:342px;top:32px;font-size:15px;font-weight:600;display:flex;gap:20px;align-items:center}
.nav .dot{width:4px;height:4px;border-radius:50%;background:var(--ink)}
/* hero */
.hero{left:0;top:124px;width:1200px;height:720px}
.hero h1{left:113px;top:150px;color:#fff;font-size:43px;line-height:51px;font-weight:600}
.hero p{color:#fff;font-size:13.5px;line-height:17px;width:410px;left:113px}
.hero .p1{top:325px}.hero .p2{top:374px}
.hero .btn{left:113px;top:438px;width:107px;height:40px;line-height:40px}
.watch{left:235px;top:438px;color:#fff;font-size:14px;font-weight:600;display:flex;align-items:center;gap:14px}
.watch .ring{width:40px;height:40px;border:2px solid var(--yellow);border-radius:50%;display:flex;align-items:center;justify-content:center}
.scroll-note{left:0;width:1200px;top:596px;text-align:center;color:#e4f1ee;font-size:13px}
/* services */
.svc-title{font-size:30px;font-weight:500;text-align:center;width:397px;top:1115px}
/* mint band */
.band{left:0;top:1234px;width:1200px;height:505px;background:var(--mint)}
.feature{left:625px;width:470px}
.feature h2{font-size:23px;font-weight:500}
.feature h2 b{font-weight:800}
.feature p{font-size:13.5px;line-height:17px;color:var(--muted);margin-top:16px;padding-left:2px}
.feature .btn{margin-top:22px;height:38px;line-height:38px;padding:0 16px;font-size:13.5px}
/* consultation */
.consult-bg{left:0;top:1739px;width:1200px;height:735px;background:linear-gradient(180deg,#f1f4f3,#e8ecea)}
.consult-panel{left:796px;top:1825px;width:404px;height:585px;background:#fff;border-radius:16px 0 0 16px}
.consult-title{left:111px;top:2000px;font-size:43px;line-height:51px;font-weight:500}
.consult-title b{font-weight:800}
.consult-phone{left:113px;top:2195px;font-size:31px;font-weight:500}
.consult-call{left:113px;top:2245px;width:107px;height:38px;line-height:38px}
.form{left:651px;top:1855px;width:370px;height:522px;background:var(--teal);border-radius:16px;padding:36px 25px}
.field{background:var(--teal-field);color:#eaf4f2;font-size:13px;height:39px;line-height:39px;padding:0 16px;border-radius:6px;margin-bottom:22px;display:flex;justify-content:space-between}
.row{display:flex;gap:20px}.row .field{flex:1}
.form .consent{color:#d7e9e6;font-size:11px;line-height:16px;margin:-6px 0 18px}
.form .btn{display:block;height:39px;line-height:39px}
/* testimonial */
.quote-h{left:744px;top:2512px;font-size:31px;line-height:38px;font-weight:500}
.quote-h b{font-weight:800}
.quote{left:744px;top:2650px;font-size:21px;line-height:24px;width:300px;color:#2b3836}
.author{left:747px;top:2750px;font-size:19px;font-weight:700}
/* footer */
.footer{left:0;top:2900px;width:1200px;height:660px;color:#fff}
.footer .brand{color:#fff}
.fnav{left:375px;top:3027px;display:flex;gap:40px;font-size:15px;font-weight:600;align-items:center;color:#fff}
.fcol{font-size:13.5px;line-height:27px;color:#d6ebe7}
.fcol h4{color:#fff;font-size:15px;font-weight:600;margin-bottom:18px}
.fcol .strong{color:#fff;font-weight:600;font-size:14.5px;margin-top:8px}
.contact{left:115px;top:3118px;font-size:13.5px;line-height:19px;color:#d6ebe7}
.contact h4{color:#fff;font-size:15px;font-weight:600;margin-bottom:24px}
.contact .lbl{color:#fff;font-weight:600;display:flex;gap:8px;align-items:center}
.contact .item{margin-bottom:14px}
.contact .item div+div{padding-left:22px}
.newsletter{left:796px;top:3115px;width:292px;color:#fff}
.newsletter h4{font-size:15px;font-weight:600}
.newsletter .input{margin-top:18px;height:48px;background:#fff;border-radius:24px;color:#9aa5a3;font-size:13px;padding:0 6px 0 16px;display:flex;align-items:center;justify-content:space-between}
.newsletter .go{width:38px;height:38px;border-radius:50%;background:var(--yellow);display:flex;align-items:center;justify-content:center}
.social{display:flex;gap:12px;margin-top:12px}
.social span{width:16px;height:16px;border-radius:50%;background:#fff}
.legal{left:113px;top:3473px;width:975px;border-top:1px solid #5c9890;padding-top:36px;font-size:13px;color:#d6ebe7;display:flex;justify-content:space-between}
</style>
</head>
<body>

<div class="abs topbar">
  <div class="abs hours"><svg width="15" height="15" viewBox="0 0 16 16"><circle cx="8" cy="8" r="7" fill="#fff"/><path d="M8 4v4l3 2" stroke="#0f6b62" stroke-width="1.6" fill="none"/></svg>Monday - Friday : 08:30 AM - 05:30 PM</div>
  <div class="abs phone">(808) 555-0172</div>
  <div class="abs btn">Call Now</div>
</div>

<div class="abs header">
  <div class="abs brand brand-l"><span class="mark"></span>Marlow</div>
  <nav class="abs nav">
    <svg width="20" height="20" viewBox="0 0 20 20"><path d="M3 9 10 3l7 6v8h-5v-5H8v5H3z" fill="#0f6b62"/></svg>
    <span class="dot"></span><span>Home Care ⌄</span><span class="dot"></span><span>Senior Living ⌄</span><span class="dot"></span><span>Rates ⌄</span><span class="dot"></span><span>About Us ⌄</span>
  </nav>
  <div class="abs brand brand-r"><span class="mark" style="background:var(--teal)"></span>Marlow</div>
</div>

<svg class="abs" style="left:0;top:124px" width="1200" height="720" viewBox="0 0 1200 720">
  <path d="M0 0H1200V600C1120 660 960 660 760 660 680 660 640 700 600 700 560 700 520 660 440 660 240 660 80 660 0 600Z" fill="#f08a76"/>
  <path d="M0 0H1200V592C1120 650 960 652 760 652 680 652 640 692 600 692 560 692 520 652 440 652 240 652 80 650 0 592Z" fill="#0f6b62"/>
  <path d="M590 631l9 6 9-6" stroke="#fff" stroke-width="1.5" fill="none"/>
  <circle cx="600" cy="684" r="32" fill="#fff"/>
  <circle cx="600" cy="684" r="28" fill="#2b3836"/>
  <rect x="591" y="668" width="18" height="30" rx="9" stroke="#fff" stroke-width="2" fill="none"/>
  <line x1="600" y1="675" x2="600" y2="682" stroke="#fff" stroke-width="2"/>
</svg>
<div class="abs hero">
  <h1 class="abs">Hawaii's choice<br>Homecare and<br>Senior living</h1>
  <p class="abs p1">Marlow Homecare provides a variety of professional in-home health care services throughout the entire island of Oahu.</p>
  <p class="abs p2">Marlow Senior Living, a beautiful Adult Residential Care Home, is located on the windward side of Oahu in Kailua.</p>
  <div class="abs btn">Contact Us</div>
  <div class="abs watch"><span class="ring"><svg width="12" height="12" viewBox="0 0 12 12"><path d="M3 1l8 5-8 5z" fill="#f5cf4f"/></svg></span>Watch Demo</div>
  <div class="abs scroll-note">Scroll to learn more</div>
</div>
<div class="abs ph" role="img" aria-label="Caregivers sharing a knitting activity with seniors on a sofa" style="left:700px;top:228px;width:347px;height:346px;background:linear-gradient(135deg,#c9b48a,#8f6a4e)"></div>
<div class="abs ph" role="img" aria-label="Caregiver and resident relaxing in a sunny living room" style="left:972px;top:189px;width:131px;height:128px;background:linear-gradient(135deg,#b5a36f,#6d5a40)"></div>
<div class="abs ph" role="img" aria-label="Caregiver walking with a senior using a walker in a garden" style="left:560px;top:466px;width:212px;height:212px;background:linear-gradient(135deg,#6f8f52,#b6b6a6)"></div>

<div class="abs ph" role="img" aria-label="Homecare aide helping a senior man in his bedroom" style="left:195px;top:870px;width:396px;height:229px;background:linear-gradient(135deg,#d8d47c,#6b5a47)"></div>
<div class="abs ph" role="img" aria-label="Residents exercising with a caregiver in a senior living lounge" style="left:608px;top:870px;width:397px;height:229px;background:linear-gradient(135deg,#a38258,#4f6f8a)"></div>
<div class="abs svc-title" style="left:194px">Homecare</div>
<div class="abs svc-title" style="left:608px">Senior Living</div>

<div class="abs band"></div>
<svg class="abs" style="left:0;top:1262px" width="1200" height="450"><path d="M4 0v450" stroke="#8aa39d" stroke-width="5" stroke-dasharray="2 9"/><path d="M1196 0v450" stroke="#8aa39d" stroke-width="5" stroke-dasharray="2 9"/></svg>
<div class="abs" role="img" aria-label="Caregiver holding a senior's hands" style="left:112px;top:1197px;width:213px;height:210px;border-radius:16px;border:3px solid var(--teal);background:linear-gradient(135deg,#f3eeea,#d9c2b2)"></div>
<div class="abs" role="img" aria-label="Caregiver serving a meal to seniors at a dining table" style="left:163px;top:1368px;width:411px;height:408px;border-radius:16px;border:3px solid #fff;background:linear-gradient(135deg,#b58e72,#5f3c2a)"></div>
<div class="abs feature" style="top:1285px">
  <h2>Professional Care In <b>Your</b> Home</h2>
  <p>Marlow Homecare understands that every person's care journey is unique. We tailor our in-home services to meet the diverse nurturing experience of professional quality care and safety within the comfort and convenience of your own home.</p>
  <span class="btn">Schedule Care Assessment</span>
</div>
<div class="abs feature" style="top:1518px">
  <h2>Trusted Care In <b>Our</b> Home</h2>
  <p>Marlow Senior Living creates a warm, supportive, and enriching care home environment where seniors can thrive in their golden years. We provide residential care that promotes well-being, connection, and dignity of each individual.</p>
  <span class="btn">Schedule Tour</span>
</div>

<div class="abs consult-bg"></div>
<div class="abs consult-panel"></div>
<h2 class="abs consult-title">Schedule a<br><b>Complimentary</b><br>Care Consultation</h2>
<div class="abs consult-phone">(808) 555-0172</div>
<div class="abs btn consult-call">Call Now</div>
<div class="abs form">
  <div class="row"><div class="field">Name</div><div class="field">Phone</div></div>
  <div class="field">Email</div>
  <div class="field">How We Can Help? <span>⌄</span></div>
  <div class="field">Question/Comments</div>
  <div class="field">How did you hear about us?</div>
  <div class="field">May We Email You About This? <span>⌄</span></div>
  <p class="consent">You agree to receive future emails and understand you may opt-out at any time</p>
  <div class="btn">Submit</div>
</div>

<div class="abs" role="img" aria-label="Caregiver and smiling senior woman looking at a tablet together" style="left:0;top:2470px;width:564px;height:350px;border-radius:0 16px 16px 0;background:linear-gradient(135deg,#e6d2bd,#b7876a)"></div>
<div class="abs" style="left:486px;top:2535px;width:224px;height:224px;border-radius:50%;background:#fff;border:2px solid var(--teal)"></div>
<div class="abs" role="img" aria-label="Portrait of owner Dana Marlow" style="left:505px;top:2554px;width:186px;height:186px;border-radius:50%;border:10px solid #f0f0f0;background:linear-gradient(135deg,#e7c9a8,#b98a5e)"></div>
<div class="abs quote-h">What Our<br><b>Owner</b> Says</div>
<svg class="abs" style="left:744px;top:2595px" width="48" height="40"><path d="M2 4h18v20L10 36H4l6-12H2zM26 4h18v20L34 36h-6l6-12h-8z" fill="#0f6b62"/></svg>
<div class="abs quote">"To care for those once cared for us is one of the highest honors."</div>
<div class="abs author">Dana Marlow</div>

<svg class="abs" style="left:0;top:2840px" width="1200" height="720" viewBox="0 0 1200 720">
  <path d="M0 140C80 70 240 60 440 60 520 60 560 20 600 20 640 20 680 60 760 60 960 60 1120 70 1200 140V720H0Z" fill="#f5cf4f"/>
  <path d="M0 150C80 78 240 68 440 68 520 68 560 28 600 28 640 28 680 68 760 68 960 68 1120 78 1200 150V720H0Z" fill="#0f6b62"/>
  <circle cx="600" cy="36" r="32" fill="#fff"/>
  <circle cx="600" cy="36" r="28" fill="#2b3836"/>
  <path d="M588 42l12-12 12 12" stroke="#fff" stroke-width="2.5" fill="none"/>
</svg>
<div class="abs footer">
  <div class="abs brand" style="left:113px;top:122px;font-size:24px"><span class="mark" style="background:#fff"></span>Marlow</div>
  <div class="abs brand" style="left:955px;top:124px;font-size:22px"><span class="mark" style="background:#fff"></span>Marlow</div>
</div>
<nav class="abs fnav">
  <svg width="18" height="18" viewBox="0 0 20 20"><path d="M3 9 10 3l7 6v8h-5v-5H8v5H3z" fill="#fff"/></svg>
  <span>Learn</span><span>Caregiver Jobs</span><span>Rates</span><span>About Us</span>
</nav>
<div class="abs contact">
  <h4>Contact Info</h4>
  <div class="item"><div class="lbl"><svg width="14" height="14" viewBox="0 0 16 16"><path d="M3 1l3 3-2 2c1 3 3 5 6 6l2-2 3 3-2 2C7 15 1 9 1 3z" fill="#fff"/></svg>Phone</div><div>(808) 555-0172 (Office)</div><div>(808) 555-0190 (After Hours)</div></div>
  <div class="item"><div class="lbl"><svg width="14" height="12" viewBox="0 0 16 12"><rect width="16" height="12" rx="1" fill="#fff"/><path d="M1 1l7 6 7-6" stroke="#0f6b62" fill="none"/></svg>Email</div><div>info@marlowhealth-example.com</div></div>
  <div class="item"><div class="lbl"><svg width="14" height="16" viewBox="0 0 14 18"><path d="M7 0a7 7 0 0 1 7 7c0 5-7 11-7 11S0 12 0 7a7 7 0 0 1 7-7z" fill="#fff"/><circle cx="7" cy="7" r="2.5" fill="#0f6b62"/></svg>Address</div><div>248 Pueo Lane, Suite 310</div><div>Honolulu, HI 96817</div></div>
</div>
<div class="abs fcol" style="left:373px;top:3118px">
  <h4>Homecare Services</h4>
  <div>Lifestyle Aide</div><div>Nurse Aide Care</div><div>Skilled Nursing</div><div>Bathing Service</div><div>Infectious Disease Care</div><div>Respite Care</div><div>Hospice Care</div>
  <div class="strong">Nures Aides</div><div class="strong">Skilled Nursing</div>
</div>
<div class="abs fcol" style="left:580px;top:3118px">
  <h4>Senior living Services</h4>
  <div>Safety and Accessibility</div><div>Healthcare Support</div><div>Social Interaction</div><div>Nutrition and Meals</div><div>Reduced Burden</div><div>Personalized Care</div><div>Engaging Activities</div><div>Peace of Mind</div><div>Transition Support</div><div>Holistic Approach</div>
</div>
<div class="abs newsletter">
  <h4>Subscribe to our Newsletter!</h4>
  <div class="input">Your email address<span class="go"><svg width="14" height="14" viewBox="0 0 14 14"><path d="M1 7h11M8 3l4 4-4 4" stroke="#1f2d2b" stroke-width="1.8" fill="none"/></svg></span></div>
  <h4 style="margin-top:32px">Follow Us on</h4>
  <div class="social"><span></span><span></span><span></span><span></span></div>
</div>
<div class="abs legal"><span>© 2023 Marlow Health Collective. All Rights Reserved.</span><span>Terms &amp; Conditions &nbsp;&nbsp;&nbsp;•&nbsp;&nbsp;&nbsp; Privacy Policy</span></div>

</body>
</html>
```